The Linen Loft Co

We need a business card design for our wardrobe company.
Please visit our website www.gentlelinenlofts.com to get an idea of who we are.

```html
<!DOCTYPE html>
<html lang="en">
<head>
<meta charset="utf-8">
<title>The Linen Loft Co – Business Card</title>
<link rel="stylesheet" href="https://fonts.googleapis.com/css2?family=Lato:wght@400;700&display=swap">
<style>
  :root {
    --backdrop: #d9d9d9;
    --card-black: #000000;
    --card-white: #ffffff;
    --text-light: #ffffff;
    --text-muted: #bdbdbd;
  }
  * { margin: 0; padding: 0; box-sizing: border-box; }
  html, body { width: 1200px; height: 802px; overflow: hidden; }
  body {
    background: var(--backdrop);
    font-family: "Lato", Arial, sans-serif;
    position: relative;
  }
  .card {
    position: absolute;
    top: 274px;
    width: 442px;
    height: 264px;
    background: var(--card-black);
    overflow: hidden;
  }
  .card--front { left: 136px; }
  .card--back { left: 624px; }

  .front-swoosh { position: absolute; inset: 0; }

  .contact-block {
    position: absolute;
    right: 21px;
    top: 115px;
    text-align: right;
    color: var(--text-light);
  }
  .person-name {
    font-size: 16px;
    font-weight: 700;
    letter-spacing: 0.3px;
    line-height: 18px;
  }
  .person-role {
    font-size: 12px;
    color: var(--text-muted);
    line-height: 15px;
  }
  .address {
    margin-top: 9px;
    font-size: 12px;
    color: var(--text-muted);
    line-height: 16px;
  }
  .contact-list {
    list-style: none;
    margin-top: 6px;
    font-size: 12px;
    color: var(--text-muted);
    line-height: 16px;
  }
  .contact-list li { display: flex; justify-content: flex-end; align-items: center; gap: 3px; }
  .contact-icon { width: 9px; height: 9px; fill: var(--text-light); }

  .brand {
    position: absolute;
    left: 127px;
    top: 110px;
    display: flex;
    align-items: center;
    gap: 12px;
    transform: translateX(-58px);
  }
  .brand-square {
    width: 46px;
    height: 46px;
    border: 1.5px solid var(--text-light);
  }
  .brand-name {
    color: var(--text-light);
    font-size: 15px;
    font-weight: 700;
    letter-spacing: 0.3px;
    line-height: 19px;
  }
  .brand-tagline {
    color: var(--text-light);
    font-size: 12px;
    font-weight: 400;
    line-height: 16px;
  }
</style>
</head>
<body>
  <section class="card card--front">
    <svg class="front-swoosh" width="442" height="264" viewBox="0 0 442 264">
      <path d="M0,0 H402 C352,70 230,115 0,150 Z" fill="var(--card-white)"/>
    </svg>
    <div class="contact-block">
      <p class="person-name">DANIEL HARTLEY</p>
      <p class="person-role">Managing Director</p>
      <p class="address">Marlow House, 24 Elm Street<br>London N4 3QT</p>
      <ul class="contact-list">
        <li>0207 555 0186
          <svg class="contact-icon" viewBox="0 0 10 10"><path d="M1,3 Q5,0 9,3 L8,4.5 L6.5,3.5 L3.5,3.5 L2,4.5 Z M2.5,5 H7.5 L8.5,9 H1.5 Z"/></svg>
        </li>
        <li>info@gentlelinenlofts.com
          <svg class="contact-icon" viewBox="0 0 10 10"><path d="M0,2 H10 V8.5 H0 Z" /><path d="M0.5,2.5 L5,6 L9.5,2.5" fill="none" stroke="#000" stroke-width="1"/></svg>
        </li>
        <li>www.gentlelinenlofts.com
          <svg class="contact-icon" viewBox="0 0 10 10"><circle cx="5" cy="5" r="4.5"/><path d="M2,4 Q4,3 4.5,5 Q6,7 7.5,6" fill="none" stroke="#000" stroke-width="1"/></svg>
        </li>
      </ul>
    </div>
  </section>

  <section class="card card--back">
    <div class="brand">
      <div class="brand-square"></div>
      <div>
        <p class="brand-name">THE LINEN LOFT CO</p>
        <p class="brand-tagline">Crafted to Fit Your Home</p>
      </div>
    </div>
  </section>
</body>
</html>
```